Simple Business Card Design for Tavlo

Job:

Make a very simple, minimalist business card design with my details including adjusted logo. One side to be white (with logo & text). Other side to be yellow - try plain or with logo (or part of logo eg Z). Need business card to have continuity with website.

Logo:
Our logo is made from a free download font website:
http://www.typewell.net/search.php?q=rubber
but the spacing/kerning needs correcting/adjusting as the font spaces unevenly between letters (see attached files). Need logo to be very crisp/sharp when printed.

Printing:
We will be using Plika.com so the design needs to conform to their requirements, see here:

http://uk.plika.com/products/luxe/business-cards.html (scroll down for dimensions and guidelines)

Design:

must say "plant-based food consulting" underneath logo or somewhere
no address needed in contact section
sharp corners (not rounded)
one side white, one side yellow

name: Rosalind Whitcombe
1xmobile number: +44 7700900463
1xtwiiter: @brimcounsel
website address www.orchardtable.com
email address brim@orchardtable.com

Should be easy quick job, prompt + detailed feedback given, am online in UK 9am-10pm for next 3 days. Website is www.orchardtable.com

Industry/Entity Type

Business

Requirements
Must have
• The logo must be corrected. The kerning is not right.

Please use a warm-grey for text

Please submit in matt format, we will be printing matt finish.

Should not have
• Avoid using banners or curvy highlights

Please avoid using black

Please avoid submitting in gloss finish

```html
<!DOCTYPE html>
<html lang="en">
<head>
<meta charset="utf-8">
<title>Brim – Business Card</title>
<link rel="stylesheet" href="https://fonts.googleapis.com/css2?family=Arimo:wght@400;700&family=Questrial&display=swap">
<style>
  :root {
    --backdrop: #5b5b5b;
    --card-white: #f7f7f6;
    --card-white-edge: #ececeb;
    --brand-yellow: #ecde2e;
    --brand-yellow-deep: #e3d12a;
    --warm-grey: #5e5a56;
    --warm-grey-light: #7a7570;
    --divider: #dcdad7;
    --logo-on-yellow: #fbfaf2;
  }
  * { box-sizing: border-box; margin: 0; padding: 0; }
  html, body {
    width: 1200px; height: 1000px; overflow: hidden;
    background: var(--backdrop);
  }
  .canvas { position: relative; width: 1200px; height: 1000px; }

  .card {
    position: absolute; top: 66px; width: 425px; height: 279px;
    box-shadow: 3px 4px 6px rgba(0,0,0,0.35);
  }
  .card--front {
    left: 131px;
    background: linear-gradient(135deg, var(--card-white), var(--card-white-edge));
  }
  .card--back {
    left: 651px;
    background: linear-gradient(160deg, var(--brand-yellow), var(--brand-yellow-deep));
  }

  .wordmark {
    position: absolute;
    font-family: "Questrial", sans-serif;
    font-weight: 400;
    line-height: 1;
    letter-spacing: 4px;
  }
  .card--front .wordmark {
    left: 30px; top: 94px; font-size: 56px; color: var(--brand-yellow);
  }
  .card--back .wordmark {
    left: 0; right: 0; top: 111px; text-align: center;
    font-size: 56px; color: var(--logo-on-yellow);
  }

  .tagline {
    position: absolute; right: 246px; top: 168px;
    font-family: "Arimo", sans-serif; font-size: 11px; line-height: 13px;
    color: var(--warm-grey); text-align: right; text-transform: uppercase;
  }

  .divider {
    position: absolute; left: 212px; top: 64px; width: 1px; height: 160px;
    background: var(--divider);
  }

  .holder-name {
    position: absolute; left: 237px; top: 95px;
    font-family: "Arimo", sans-serif; font-weight: 700; font-size: 14px;
    color: var(--warm-grey); text-transform: uppercase; letter-spacing: 0.3px;
  }

  .contact-list {
    position: absolute; left: 236px; top: 132px; list-style: none;
    font-family: "Questrial", sans-serif; font-size: 11.5px; color: var(--warm-grey-light);
  }
  .contact-list li { display: flex; align-items: center; height: 16px; }
  .contact-list svg { width: 10px; height: 10px; margin-right: 6px; flex: none; }
  .contact-list svg * { fill: none; stroke: var(--brand-yellow); stroke-width: 1.2; }
</style>
</head>
<body>
<main class="canvas">
  <section class="card card--front" aria-label="Business card front">
    <div class="wordmark">BRIM</div>
    <p class="tagline">Plant-based<br>food consulting</p>
    <div class="divider"></div>
    <h1 class="holder-name">Rosalind Whitcombe</h1>
    <ul class="contact-list">
      <li>
        <svg viewBox="0 0 10 10" aria-hidden="true"><path d="M2 1.5 L3.6 1.5 L4.2 3.3 L3.2 4 Q4.2 6 6 6.8 L6.7 5.8 L8.5 6.4 L8.5 8 Q5 8.5 2.8 6.3 Q1 4.3 2 1.5Z"/></svg>
        +44 7700900463
      </li>
      <li>
        <svg viewBox="0 0 10 10" aria-hidden="true"><circle cx="5" cy="5" r="4.2"/></svg>
        @brimcounsel
      </li>
      <li>
        <svg viewBox="0 0 10 10" aria-hidden="true"><rect x="1" y="2.2" width="8" height="5.6"/><path d="M1 2.2 L5 5.5 L9 2.2"/></svg>
        brim@orchardtable.com
      </li>
      <li>
        <svg viewBox="0 0 10 10" aria-hidden="true"><circle cx="5" cy="5" r="4.2"/><ellipse cx="5" cy="5" rx="1.8" ry="4.2"/><path d="M0.8 5 H9.2"/></svg>
        www.orchardtable.com
      </li>
    </ul>
  </section>

  <section class="card card--back" aria-label="Business card back">
    <div class="wordmark">BRIM</div>
  </section>
</main>
</body>
</html>
```